Clean business card with logo provided

I want a card that will stand out among the masses. I need the color and image to show professionalism and yet have a family appeal showing that I only deal with win/win scenarios. The back of the card will be used to take notes about the individual so I can use that in my database entry. I like modern design but need professionalism in it also. It needs to fit my "clean, safe, and affordable housing" motto. I need to be able to write on the file and update the card details for my employees.

Target Market(s)

Investors looking to make investment income through real estate

Industry/Entity Type

Real Estate

Contact Information for Business Card

Brent Kovalich
blank address, city, st, zip code
480-555-3174
brentkovalich@ridgeworthrentals.example
www.ridgeworthrentals.example

Font styles to use
Sans Serif

Requirements
Must have
• I would like the back of the card to have lines for info. example
• Met/Visited: Date:
• Interets:
Nice to have
• I want the cards color to match the logo background color. Font with details to be san serif and black. I want the card rectangular with square corners. Standard business card size. I would like to see cards designed with both images to see which i prefer more.

```html
<!DOCTYPE html>
<html lang="en">
<head>
<meta charset="utf-8">
<title>Ridgeworth Rentals LLC – Business Card</title>
<link rel="stylesheet" href="https://fonts.googleapis.com/css2?family=Open+Sans:wght@400;600&display=swap">
<style>
  :root {
    --backdrop: #3a3531;
    --card: #141414;
    --teal: #20b4c8;
    --light: #e6e6e6;
    --muted: #bdbdbd;
    --rule: #d8d8d8;
    --silver: #8d8d8d;
  }
  * { box-sizing: border-box; margin: 0; padding: 0; }
  html, body { width: 1200px; height: 814px; overflow: hidden; }
  body {
    background: var(--backdrop);
    font-family: "Open Sans", Arial, sans-serif;
    display: flex;
    align-items: center;
    justify-content: center;
    gap: 40px;
  }
  .card {
    position: relative;
    width: 540px;
    height: 309px;
    background: var(--card);
    color: var(--light);
    overflow: hidden;
  }

  /* Front */
  .brand {
    position: absolute;
    top: 56px;
    left: 0;
    right: 0;
    text-align: center;
  }
  .brand-name {
    display: inline-flex;
    align-items: center;
    gap: 10px;
    font-size: 26px;
    font-weight: 400;
    letter-spacing: 3px;
    color: var(--teal);
  }
  .brand-dot {
    width: 14px; height: 14px; border-radius: 50%;
    background: var(--teal);
  }
  .brand-motto {
    margin-top: 6px;
    font-size: 10px;
    color: var(--teal);
    letter-spacing: 0.5px;
  }
  .owner {
    position: absolute;
    left: 20px;
    top: 188px;
    width: 190px;
    text-align: right;
  }
  .owner-name { font-size: 19px; font-weight: 600; color: var(--teal); white-space: nowrap; }
  .owner-address { font-size: 13px; line-height: 1.5; color: var(--muted); margin-top: 4px; white-space: nowrap; }
  .divider {
    position: absolute;
    left: 226px; top: 170px;
    width: 1px; height: 104px;
    background: var(--silver);
  }
  .contacts {
    position: absolute;
    left: 242px; top: 174px;
    right: 16px;
    list-style: none;
    font-size: 12.5px;
    color: var(--light);
  }
  .contacts li { display: flex; align-items: center; gap: 8px; height: 22px; white-space: nowrap; }
  .contacts svg { width: 13px; height: 13px; flex: none; }

  /* Back */
  .brand-back {
    position: absolute;
    top: 30px; left: 0; right: 0;
    text-align: center;
  }
  .brand-back .brand-name { color: var(--silver); font-size: 22px; }
  .brand-back .brand-motto { color: var(--silver); font-size: 9px; }
  .notes {
    position: absolute;
    left: 36px; right: 36px; top: 112px;
    list-style: none;
  }
  .notes li {
    display: flex;
    align-items: flex-end;
    gap: 8px;
    height: 34px;
  }
  .notes-label {
    font-size: 12px;
    font-weight: 600;
    color: var(--teal);
    letter-spacing: 0.5px;
    white-space: nowrap;
    line-height: 1;
  }
  .notes-line {
    flex: 1;
    border-bottom: 1px solid var(--rule);
    margin-bottom: 1px;
  }
</style>
</head>
<body>

  <section class="card card-front" aria-label="Card front">
    <div class="brand">
      <div class="brand-name"><span class="brand-dot"></span>RIDGEWORTH RENTALS LLC</div>
      <p class="brand-motto">Providing clean, safe, and affordable housing</p>
    </div>

    <div class="owner">
      <p class="owner-name">Brent Kovalich</p>
      <p class="owner-address">4120 Juniper Court<br>Fairbanks, Alaska 99701</p>
    </div>

    <div class="divider"></div>

    <ul class="contacts">
      <li>
        <svg viewBox="0 0 16 16" aria-hidden="true"><path fill="var(--teal)" d="M3.6 1.5l2.3 2.6-1.2 1.8a9 9 0 0 0 5.4 5.4l1.8-1.2 2.6 2.3-1.4 2.1C7.5 14.4 1.6 8.5 1.5 2.9z"/></svg>
        480-555-3174
      </li>
      <li>
        <svg viewBox="0 0 16 16" aria-hidden="true"><rect x="1" y="3" width="14" height="10" rx="1" fill="var(--teal)"/><path d="M1.5 3.8L8 9l6.5-5.2" fill="none" stroke="var(--card)" stroke-width="1.3"/></svg>
        brentkovalich@ridgeworthrentals.example
      </li>
      <li>
        <svg viewBox="0 0 16 16" aria-hidden="true"><circle cx="8" cy="8" r="7" fill="var(--teal)"/><path d="M1 8h14M8 1c-3 3.5-3 10.5 0 14M8 1c3 3.5 3 10.5 0 14" fill="none" stroke="var(--card)" stroke-width="1"/></svg>
        www.ridgeworthrentals.example
      </li>
    </ul>
  </section>

  <section class="card card-back" aria-label="Card back">
    <div class="brand-back">
      <div class="brand-name">RIDGEWORTH RENTALS LLC</div>
      <p class="brand-motto">Providing clean, safe, and affordable housing</p>
    </div>

    <ul class="notes">
      <li><span class="notes-line"></span></li>
      <li><span class="notes-label">MET/VISITED:</span><span class="notes-line"></span></li>
      <li><span class="notes-label">DATE:</span><span class="notes-line"></span></li>
      <li><span class="notes-label">INTERESTS:</span><span class="notes-line"></span></li>
      <li><span class="notes-line"></span></li>
    </ul>
  </section>

</body>
</html>
```